Werbetafel für Immobilienverwaltung
Zielgruppe
Wir sind im Kern eine Immobilienverwaltung, daher richten wir uns an Eigentümer/Investoren/Kapitalanleger. Neben der Verwaltung welche auch durch Hausmeisterservice (Grünarbeiten usw.) erweitert werden kann, bieten wir die Gutachtenerstellung sowie den Vertrieb (Maklertätigkeit in Verkauf sowie Vermietung) an.
Ein großer Vorteil ist unsere Digitale Arbeitsweise (noch keine Selbstverständlichkeit in der Branche).
Aufgabenstellung
Ziel ist es, das Unternehmen unaufdringlich jedoch wirksam und informativ auf einer Werbetafel zu präsentieren.
Maße der Tafel, welche sich im ausgangsbereich eines großen Lebensmittelunternehmens befindet, ist B 320cm x H 120cm.
Die Kundschaft läuft in ca. 1m Entfernung an der Tafel vorbei, sie sollte also von nahem nicht zu überrumpelt wirken.
Unser Logo sowie Telefonnummer sollte iwie untergebracht werden.
Gern auch eigene Ideen umsetzen falls Ihr welche habt.

```html
<!DOCTYPE html>
<html lang="de">
<head>
<meta charset="utf-8">
<title>Valmoor Immobilien – Werbetafel</title>
<link href="https://fonts.googleapis.com/css2?family=Figtree:wght@400;700;800&display=swap" rel="stylesheet">
<style>
  :root {
    --brand-red: #93201f;
    --text-grey: #58585a;
    --band-grey: #f2f2f4;
    --page-bg: #f2f2f2;
    --board-bg: #ffffff;
  }
  * { margin: 0; padding: 0; box-sizing: border-box; }
  html, body {
    width: 1200px; height: 960px; overflow: hidden;
    background: var(--page-bg);
    font-family: "Figtree", "Helvetica Neue", Arial, sans-serif;
  }
  .billboard {
    position: absolute; left: 61px; top: 144px;
    width: 1077px; height: 673px;
    background: var(--board-bg);
    overflow: hidden;
  }
  .billboard__shapes { position: absolute; inset: 0; }
  .headline {
    position: absolute; left: 77px; top: 62px;
    font-weight: 800; font-size: 90px; line-height: 93px;
    letter-spacing: -0.5px;
  }
  .headline__lead { color: var(--brand-red); display: block; }
  .headline__tail { color: var(--text-grey); display: block; }
  .call-label {
    position: absolute; left: 73px; top: 452px;
    color: var(--brand-red); font-weight: 800; font-size: 46px; line-height: 56px;
  }
  .phone-number {
    position: absolute; left: 74px; top: 530px;
    color: #fff; font-weight: 800; font-size: 72px; line-height: 80px;
    letter-spacing: -1px;
  }
  .company-name {
    position: absolute; left: 688px; top: 544px;
    display: flex; align-items: center; gap: 12px;
    white-space: nowrap;
    color: var(--brand-red); font-weight: 700; font-size: 33px; line-height: 44px;
  }
  .company-name__dot {
    width: 20px; height: 20px; border-radius: 50%; background: var(--brand-red);
    flex: none;
  }
</style>
</head>
<body>
  <main class="billboard">
    <svg class="billboard__shapes" width="1077" height="673" viewBox="0 0 1077 673" aria-hidden="true">
      <polygon points="0,403 847,403 804,673 0,673" fill="var(--band-grey)"/>
      <polygon points="0,516 663,516 646,628 0,628" fill="var(--brand-red)"/>
    </svg>

    <h1 class="headline">
      <span class="headline__lead">Ihre Immobilie -</span>
      <span class="headline__tail">unser Know-Haus</span>
    </h1>

    <p class="call-label">Jetzt anrufen</p>
    <p class="phone-number">0391 480 27 63</p>

    <div class="company-name"><span class="company-name__dot"></span>Valmoor Immobilien</div>
  </main>
</body>
</html>
```